Website Revamp: Bravoly.com

Just got a new logo looking for a web design to go with the business. I need the photoshop files and stock photos. No Word Press Please.

```html
<!DOCTYPE html>
<html lang="en">
<head>
<meta charset="utf-8">
<title>Bravoly Auto Recycling</title>
<link href="https://fonts.googleapis.com/css2?family=Poppins:ital,wght@0,400;0,500;0,600;0,700;1,800&display=swap" rel="stylesheet">
<style>
:root{
  --green:#8cc63f;
  --green-dark:#5e9322;
  --grey:#7b8386;
  --ink:#2b2b2b;
  --text:#6d6d6d;
  --dark:#3b3c3e;
  --white:#ffffff;
}
*{margin:0;padding:0;box-sizing:border-box}
html,body{width:1200px;height:4092px;overflow:hidden}
body{position:relative;background:var(--white);font-family:'Poppins',sans-serif;color:var(--ink)}
.abs{position:absolute}
a{color:inherit;text-decoration:none}

/* header */
.brand{display:flex;align-items:center;gap:14px}
.brand-dot{width:58px;height:58px;border-radius:50%;background:var(--green)}
.brand-name{font-weight:700;font-size:30px;color:var(--green);letter-spacing:1px}
.contact-top{top:28px;right:112px;display:flex;gap:22px;font-size:17px;align-items:center}
.contact-top span{display:flex;align-items:center;gap:10px}
.ico-round{width:36px;height:36px;border-radius:50%;background:var(--green);display:flex;align-items:center;justify-content:center}
.nav{top:88px;right:112px;display:flex;gap:26px;font-size:17px}
.nav .active{color:var(--green)}

/* hero */
.hero{top:133px;left:0;width:1200px;height:720px}
.hero-title{top:272px;right:112px;text-align:right;color:var(--white)}
.hero-title h1{font-weight:800;font-style:italic;font-size:86px;line-height:1;letter-spacing:2px}
.hero-title p{font-weight:800;font-style:italic;font-size:36px;letter-spacing:14px;margin-top:14px}
.btn{display:inline-flex;align-items:center;justify-content:center;border-radius:28px;color:var(--white);font-size:16px}
.btn-hero{top:450px;left:950px;width:138px;height:56px;background:var(--green);border:3px solid var(--white);font-size:18px}

/* headings */
.eyebrow{font-size:19px;text-transform:uppercase;text-align:center;width:1200px;left:0}
.heading{font-size:38px;font-weight:600;text-align:center;width:1200px;left:0;color:var(--green)}

/* cards */
.card{top:1044px;width:474px;height:363px;background:var(--white);box-shadow:0 0 12px rgba(0,0,0,.14)}
.card-photo{position:absolute;left:11px;top:11px;width:183px;height:342px}
.card-body{position:absolute;left:218px;top:34px;width:236px}
.card-body h3{font-size:20px;font-weight:500;color:#333}
.card-body p{font-size:13px;line-height:24px;color:var(--text);text-align:justify;margin-top:10px}
.btn-card{margin-top:24px;width:111px;height:44px;background:var(--grey);font-size:14px}

/* recycle section */
.recycle-bg{top:1480px;left:0}
.cat{top:1764px;width:260px;text-align:center;color:var(--white)}
.cat-circle{width:170px;height:170px;border-radius:50%;border:8px solid var(--white);background:var(--grey);margin:0 auto;display:flex;align-items:center;justify-content:center}
.cat-circle.on{background:var(--green-dark)}
.cat-arrow{width:0;height:0;border-left:8px solid transparent;border-right:8px solid transparent;border-top:13px solid var(--white);margin:12px auto 0}
.cat h4{font-size:25px;font-weight:600;margin-top:14px;white-space:nowrap}
.recycle-copy{top:2072px;left:112px;width:976px;color:var(--white);font-size:15px;line-height:26px;text-align:center}

/* about */
.about-art{top:2429px;left:111px;width:374px;height:377px}
.about-text{top:2430px;left:583px;width:505px}
.about-text .eyebrow-l{font-size:19px}
.about-text h2{font-size:42px;font-weight:600;color:var(--green);line-height:1.2}
.about-text p{font-size:13px;line-height:24px;color:var(--text);margin-top:18px}
.btn-about{margin-top:30px;width:134px;height:52px;background:var(--green);font-size:18px}

/* process */
.process-bg{top:2870px;left:0}
.step{top:3152px;width:300px;text-align:center;color:var(--white)}
.step-circle{width:246px;height:246px;border-radius:50%;border:8px solid var(--white);margin:0 auto;display:flex;flex-direction:column;align-items:center;justify-content:center;gap:14px}
.step-circle.grey{background:var(--grey)}
.step-circle.green{background:var(--green)}
.step-circle h4{font-size:21px;font-weight:600;line-height:30px}
.step p{font-size:13px;line-height:25px;margin-top:18px}
.play{width:0;height:0;border-top:19px solid transparent;border-bottom:19px solid transparent;border-left:32px solid var(--white)}

/* footer */
.foot-brand{top:3790px;left:111px;display:flex;flex-direction:column;align-items:center;gap:14px;width:200px}
.foot-col h5{font-size:20px;font-weight:500;margin-bottom:14px}
.foot-col li{list-style:none;font-size:15px;line-height:27.6px;color:#555}
.contact-row{display:flex;align-items:center;gap:18px;font-size:15px;color:#555;line-height:22px}
.divider{top:4015px;left:111px;width:978px;height:1px;background:#cfcfcf}
.copyright{top:4043px;left:0;width:1200px;text-align:center;font-size:14px}
</style>
</head>
<body>

<header>
  <div class="abs brand" style="top:24px;left:111px">
    <span class="brand-dot"></span><span class="brand-name">Bravoly</span>
  </div>
  <div class="abs contact-top">
    <span><span class="ico-round"><svg width="18" height="18" viewBox="0 0 24 24" fill="none" stroke="#fff" stroke-width="2"><path d="M5 3h4l2 5-2.5 1.5a11 11 0 0 0 6 6L16 13l5 2v4a2 2 0 0 1-2 2A16 16 0 0 1 3 5a2 2 0 0 1 2-2z"/></svg></span>+1 555 014 2288</span>
    <span><span class="ico-round"><svg width="18" height="18" viewBox="0 0 24 24" fill="none" stroke="#fff" stroke-width="2"><rect x="3" y="5" width="18" height="14" rx="1"/><path d="M3 6l9 7 9-7"/></svg></span>info@bravoly.com</span>
  </div>
  <nav class="abs nav">
    <a class="active">Home</a><a>Our Services</a><a>Recycle</a><a>About Us</a><a>Blog</a><a>Contact Us</a>
  </nav>
</header>

<section>
  <svg class="abs hero" viewBox="0 0 1200 720" role="img" aria-label="Photo of a rusted red pickup truck parked among green foliage">
    <defs>
      <linearGradient id="heroGrad" x1="0" y1="0" x2="0" y2="1">
        <stop offset="0" stop-color="#3d5a2a"/>
        <stop offset=".45" stop-color="#5f7a45"/>
        <stop offset=".75" stop-color="#6e6a63"/>
        <stop offset="1" stop-color="#8a8784"/>
      </linearGradient>
    </defs>
    <rect width="1200" height="720" fill="url(#heroGrad)"/>
    <path d="M0 614 C250 560 560 690 900 700 C1020 704 1120 640 1200 567 L1200 720 L0 720Z" fill="#fff"/>
    <path d="M30 620 C300 480 600 720 900 690 C980 680 1030 620 1040 545 C1030 650 970 712 880 712 C600 735 300 565 30 620Z" fill="#8cc63f"/>
  </svg>
  <div class="abs hero-title"><h1>BRAVOLY</h1><p>AUTO RECYCLING</p></div>
  <a class="abs btn btn-hero">Read More</a>
</section>

<section>
  <p class="abs eyebrow" style="top:914px">About</p>
  <h2 class="abs heading" style="top:938px">WHY RECYCLE WITH BRAVOLY</h2>

  <article class="abs card" style="left:111px">
    <svg class="card-photo" role="img" aria-label="Photo of salvaged car doors stacked on shelves"><rect width="100%" height="100%" fill="#4a5160"/></svg>
    <div class="card-body">
      <h3>NEMO ENIM IPSAM</h3>
      <p>Sed ut perspiciatis unde omnis iste natus error sit voluptatem ac cusantium doloremque laudan tium, totam rem aperiam nim ad minima veniam, quis nostrum ex ercitationem ullam corporis sus cipit laboriosam, nisi ut aliquid ex ea commodis.</p>
      <a class="btn btn-card">Read More</a>
    </div>
  </article>
  <article class="abs card" style="left:613px">
    <svg class="card-photo" role="img" aria-label="Photo of scrapped cars stacked in a yard"><rect width="100%" height="100%" fill="#7c7a6a"/></svg>
    <div class="card-body">
      <h3>NEMO ENIM IPSAM</h3>
      <p>Sed ut perspiciatis unde omnis iste natus error sit voluptatem ac cusantium doloremque laudan tium, totam rem aperiam nim ad minima veniam, quis nostrum ex ercitationem ullam corporis sus cipit laboriosam, nisi ut aliquid ex ea commodis.</p>
      <a class="btn btn-card">Read More</a>
    </div>
  </article>
</section>

<section>
  <svg class="abs recycle-bg" width="1200" height="880" viewBox="0 0 1200 880" role="img" aria-label="Green tinted photo of a scrap car yard">
    <path d="M0 110 C90 60 180 10 300 16 C560 30 900 60 1200 120 L1200 760 C1100 820 1000 860 880 850 C600 820 300 710 0 700Z" fill="#8cc63f"/>
  </svg>
  <p class="abs eyebrow" style="top:1610px;color:#fff;font-size:18px">Bravoly</p>
  <h2 class="abs heading" style="top:1640px;color:#fff">WHAT ALL DO WE RECYCLE?</h2>

  <div class="abs cat" style="left:70px">
    <div class="cat-circle"><svg width="74" height="74" viewBox="0 0 48 48" fill="none" stroke="#fff" stroke-width="2.4"><path d="M10 22l4-10h20l4 10"/><rect x="6" y="22" width="36" height="12" rx="2"/><path d="M10 34v5h5v-5M33 34v5h5v-5M17 28h14M11 28h2M35 28h2"/></svg></div>
    <div class="cat-arrow"></div><h4>CARS</h4>
  </div>
  <div class="abs cat" style="left:328px">
    <div class="cat-circle on"><svg width="74" height="74" viewBox="0 0 48 48" fill="none" stroke="#fff" stroke-width="2.4"><rect x="12" y="5" width="24" height="34" rx="3"/><path d="M12 18h24M16 10h16M16 27h5M27 27h5M16 32h16M15 39v4h4v-4M29 39v4h4v-4M9 14h3M36 14h3"/></svg></div>
    <div class="cat-arrow"></div><h4>TRUCKS &amp; BUSES</h4>
  </div>
  <div class="abs cat" style="left:585px">
    <div class="cat-circle"><svg width="84" height="84" viewBox="0 0 48 48" fill="none" stroke="#fff" stroke-width="2.4"><circle cx="12" cy="30" r="8"/><circle cx="36" cy="30" r="8"/><path d="M12 30l7-12h12l5 12M19 18l7 12h10M17 15h6M29 13h5"/></svg></div>
    <div class="cat-arrow"></div><h4>TWO WEELERS</h4>
  </div>
  <div class="abs cat" style="left:841px">
    <div class="cat-circle"><svg width="80" height="80" viewBox="0 0 48 48" fill="none" stroke="#fff" stroke-width="2.4"><path d="M6 32l6-12h12l4 8M22 24l6-10h12l4 10v10H22z"/><circle cx="12" cy="36" r="4"/><circle cx="28" cy="36" r="4"/><circle cx="40" cy="36" r="4"/></svg></div>
    <div class="cat-arrow"></div><h4>INSUSTRIAL SCRAP</h4>
  </div>

  <p class="abs recycle-copy">Nemo enim ipsam voluptatem quia voluptas sit aspernatur aut odit aut fugit, sed quia consequuntur magni dolores eos qui ra tione voluptatem sequi nesciunt. Neque porro quisquam est, qui dolorem ipsum quia dolor sit amet, consectetur, adipisci velit, sed quia non numquam.</p>
</section>

<section>
  <svg class="abs about-art" viewBox="0 0 374 377" role="img" aria-label="Illustration of a car inside a green and grey recycling loop">
    <defs><radialGradient id="artGrad"><stop offset="0" stop-color="#c7e39a"/><stop offset="1" stop-color="#8cc63f"/></radialGradient></defs>
    <rect width="374" height="377" rx="30" fill="url(#artGrad)"/>
  </svg>
  <div class="abs about-text">
    <p class="eyebrow-l">ABOUT</p>
    <h2>BRAVOLY</h2>
    <p>Nemo enim ipsam voluptatem quia voluptas sit aspernatur aut odit aut fugit, sed quia consequuntur magni dolores eos qui ratione voluptatem sequi nesciunt. Neque porro quisquam est, qui dolorem ipsum quia dolor sit amet, consectetur, adipisci velit, sed quia non numquam.</p>
    <p style="margin-top:14px">Quis autem vel eum iure reprehenderit qui in ea voluptate velit esse quam nihil molestiae consequatur, vel illum qui dolorem eum fugiat quo volup tas nulla par iatur sed quia non numquam.</p>
    <a class="btn btn-about">Read More</a>
  </div>
</section>

<section>
  <svg class="abs process-bg" width="1200" height="860" viewBox="0 0 1200 860" role="img" aria-label="Dark tinted photo of a pile of scrap metal">
    <path d="M0 135 C300 80 650 20 900 10 C1040 4 1140 20 1200 40 L1200 790 C1100 830 1000 850 950 850 C600 850 300 700 0 660Z" fill="#3b3c3e"/>
  </svg>
  <p class="abs eyebrow" style="top:3010px;color:#fff;font-size:18px">Our</p>
  <h2 class="abs heading" style="top:3036px;color:#fff">RECYCLING PROCESS</h2>

  <div class="abs step" style="left:112px">
    <div class="step-circle grey">
      <svg width="70" height="62" viewBox="0 0 48 42" fill="none" stroke="#fff" stroke-width="2.2"><path d="M6 18l4-10h18l4 10"/><rect x="3" y="18" width="30" height="11" rx="2"/><circle cx="36" cy="28" r="7"/><circle cx="36" cy="28" r="2.5"/></svg>
      <h4>GET DETAILS<br>OF CAR</h4>
    </div>
    <p>Nemo enim ipsam voluptatem quia volup tas sit aspernatur aut odit aut fugit, sed quia consequuntur magnis</p>
  </div>
  <div class="abs play" style="top:3256px;left:416px"></div>
  <div class="abs step" style="left:450px">
    <div class="step-circle green">
      <svg width="66" height="66" viewBox="0 0 48 48" fill="none" stroke="#fff" stroke-width="2.2"><path d="M24 4l5 6 7-2 1 8 7 3-4 6 4 6-7 3-1 8-7-2-5 6-5-6-7 2-1-8-7-3 4-6-4-6 7-3 1-8 7 2z"/><path d="M18 30l12-12"/><circle cx="19" cy="19" r="2"/><circle cx="29" cy="29" r="2"/></svg>
      <h4>LET YOU KNOW<br>OFFERS</h4>
    </div>
    <p>Nemo enim ipsam voluptatem quia volup tas sit aspernatur aut odit aut fugit, sed quia consequuntur magnis</p>
  </div>
  <div class="abs play" style="top:3256px;left:752px"></div>
  <div class="abs step" style="left:788px">
    <div class="step-circle grey">
      <svg width="66" height="72" viewBox="0 0 48 52" fill="none" stroke="#fff" stroke-width="2.2"><path d="M24 22s-8-7-8-13a8 8 0 0 1 16 0c0 6-8 13-8 13z"/><circle cx="24" cy="9" r="3"/><path d="M8 34l4-8h24l4 8"/><rect x="5" y="34" width="38" height="10" rx="2"/><path d="M9 44v4h5v-4M34 44v4h5v-4"/></svg>
      <h4>PICK UP PLACE<br>OF PRODUCT</h4>
    </div>
    <p>Nemo enim ipsam voluptatem quia volup tas sit aspernatur aut odit aut fugit, sed quia consequuntur magnis</p>
  </div>
</section>

<footer>
  <div class="abs foot-brand">
    <span class="brand-dot" style="width:96px;height:96px"></span>
    <span class="brand-name" style="font-size:34px">Bravoly</span>
  </div>
  <div class="abs foot-col" style="top:3750px;left:378px">
    <h5>QUICK LINKS</h5>
    <div style="display:flex;gap:68px">
      <ul><li>Home</li><li>Services</li><li>Recycle</li><li>About Us</li><li>Blog</li><li>Contact Us</li></ul>
      <ul><li>Quis nostrum</li><li>Exercitationem</li><li>Ullam corporis</li><li>Suscipit</li></ul>
    </div>
  </div>
  <div class="abs foot-col" style="top:3750px;left:690px;width:400px">
    <h5>CONTACT US</h5>
    <div class="contact-row"><span class="ico-round" style="flex:none"><svg width="18" height="18" viewBox="0 0 24 24" fill="none" stroke="#fff" stroke-width="2"><path d="M12 21s-7-6-7-12a7 7 0 0 1 14 0c0 6-7 12-7 12z"/><circle cx="12" cy="9" r="2.5"/></svg></span><span>Nemo enim ipsam voluptatem quia voluptas sit aspernatur aut odit aut fugit, sed quia</span></div>
    <div class="contact-row" style="margin-top:26px"><span class="ico-round"><svg width="18" height="18" viewBox="0 0 24 24" fill="none" stroke="#fff" stroke-width="2"><path d="M5 3h4l2 5-2.5 1.5a11 11 0 0 0 6 6L16 13l5 2v4a2 2 0 0 1-2 2A16 16 0 0 1 3 5a2 2 0 0 1 2-2z"/></svg></span><span>Phone: +1 555 014 2288</span></div>
    <div class="contact-row" style="margin-top:24px"><span class="ico-round"><svg width="18" height="18" viewBox="0 0 24 24" fill="none" stroke="#fff" stroke-width="2"><rect x="3" y="5" width="18" height="14" rx="1"/><path d="M3 6l9 7 9-7"/></svg></span><span>Mail:info@bravoly.com</span></div>
  </div>
  <div class="abs divider"></div>
  <p class="abs copyright">Copyrights @ 2020 Bravoly Auto Recycling. All Rights Reserved.</p>
</footer>

</body>
</html>
```